Brightwave Reach - Business Card

We need a business card for a Social Media Marketing company that specializes in online marketing for small businesses in Canada using common Social Media platforms such as Pixlora, Chatterly, Blinkpost & Quibber.

I have uploaded a copy of our logo which I would like utilized in the business card. We would like the business card to be modern yet classy design.

Our website is www.brightwavereach.ca

Industry/Entity Type

Marketing

Contact Information for Business Card

Email: info@brightwavereach.ca
Website: www.brightwavereach.ca
Telephone: 604-555-0193

Colors

Designer to choose colors to be used in the design.

Requirements
Must have
• Social Media icons on reverse
• Please add some designs with color.

```html
<!DOCTYPE html>
<html lang="en">
<head>
<meta charset="UTF-8">
<title>Brightwave Reach – Business Card</title>
<link href="https://fonts.googleapis.com/css2?family=Roboto:wght@400;500&family=Roboto+Condensed:wght@500;700&display=swap" rel="stylesheet">
<style>
  :root {
    --backdrop: #e3e3e3;
    --card-light: #f2f2f2;
    --card-dark: #3b3e41;
    --ink: #3a3d40;
    --ink-soft: #a2a2a2;
    --stripe: #acacac;
    --white: #ffffff;
    --rule: #d0d0d0;
  }
  * { margin: 0; padding: 0; box-sizing: border-box; }
  html, body {
    width: 1200px; height: 960px; overflow: hidden;
    background: var(--backdrop);
  }
  .canvas { position: relative; width: 1200px; height: 960px; }

  .card { position: absolute; width: 600px; height: 342px; overflow: hidden; }
  .card-front { left: 314px; top: 113px; background: var(--card-light); }
  .card-back { left: 311px; top: 472px; background: var(--card-dark); height: 343px; }

  .brand-mark {
    position: absolute; left: 82px; top: 122px; width: 200px;
    text-align: center;
    font-family: "Roboto Condensed", Arial, sans-serif;
    font-weight: 700; font-size: 30px; line-height: 31px;
    color: var(--ink); text-transform: uppercase;
  }

  .divider {
    position: absolute; left: 306px; top: 87px; width: 1px; height: 158px;
    background: var(--rule);
  }

  .person {
    position: absolute; left: 343px; top: 112px;
    font-family: "Roboto Condensed", Arial, sans-serif;
  }
  .person-name { font-size: 21px; font-weight: 500; color: var(--ink); line-height: 26px; }
  .person-title { font-family: "Roboto", Arial, sans-serif; font-size: 14px; color: var(--ink-soft); line-height: 18px; }

  .contact-list {
    position: absolute; left: 343px; top: 181px; list-style: none;
    font-family: "Roboto", Arial, sans-serif; font-size: 14px; color: var(--ink);
  }
  .contact-list li { display: flex; align-items: center; height: 20px; }
  .contact-list svg { width: 12px; height: 12px; margin-right: 10px; fill: var(--ink); }

  .footer-band { position: absolute; left: 0; bottom: 0; width: 600px; height: 36px; }
  .website {
    position: absolute; right: 28px; bottom: 11px;
    font-family: "Roboto", Arial, sans-serif; font-size: 14px; letter-spacing: 1.2px;
    color: var(--white);
  }

  .back-brand {
    position: absolute; left: 270px; top: 196px; width: 312px;
    text-align: center;
    font-family: "Roboto Condensed", Arial, sans-serif; font-weight: 700;
    font-size: 44px; line-height: 40px; color: var(--white); text-transform: uppercase;
  }
  .social-row {
    position: absolute; left: 280px; top: 289px; width: 296px; height: 22px;
    display: flex; align-items: center; gap: 8px;
    font-family: "Roboto", Arial, sans-serif; font-size: 11px; color: var(--white);
  }
  .social-row .line { flex: 1; height: 1px; background: #9a9c9e; }
  .social-item { display: flex; align-items: center; gap: 4px; }
  .social-item .dot { width: 10px; height: 10px; border: 1px solid var(--white); border-radius: 50%; }
</style>
</head>
<body>
<main class="canvas">

  <section class="card card-front" aria-label="Business card front">
    <div class="brand-mark">Brightwave<br>Reach</div>
    <div class="divider"></div>

    <div class="person">
      <div class="person-name">DANIEL REEVE</div>
      <div class="person-title">CEO/FOUNDER</div>
    </div>

    <ul class="contact-list">
      <li>
        <svg viewBox="0 0 24 24" aria-hidden="true"><path d="M6.6 10.8a15.1 15.1 0 0 0 6.6 6.6l2.2-2.2c.3-.3.7-.4 1-.2 1.1.4 2.3.6 3.6.6.6 0 1 .4 1 1V20c0 .6-.4 1-1 1A17 17 0 0 1 3 4c0-.6.4-1 1-1h3.5c.6 0 1 .4 1 1 0 1.3.2 2.5.6 3.6.1.3 0 .7-.2 1z"/></svg>
        604-555-0193
      </li>
      <li>
        <svg viewBox="0 0 24 24" aria-hidden="true"><path d="M2 5h20v14H2z M2 5l10 8 10-8" /></svg>
        info@brightwavereach.ca
      </li>
    </ul>

    <svg class="footer-band" viewBox="0 0 600 36" aria-hidden="true">
      <path d="M0 4 H356 Q350 4 346 14 H0 Z" fill="var(--stripe)"/>
      <path d="M0 14 H352 Q358 14 362 8 L366 2 Q368 0 372 0 H600 V36 H0 Z" fill="var(--card-dark)"/>
      <path d="M0 14 H352 Q358 14 362 8 L366 2 Q368 0 372 0 H600" fill="none" stroke="var(--white)" stroke-width="1.5"/>
    </svg>
    <div class="website">www.brightwavereach.ca</div>
  </section>

  <section class="card card-back" aria-label="Business card back">
    <div class="back-brand">Brightwave<br>Reach</div>
    <div class="social-row">
      <span class="line"></span>
      <span class="social-item"><span class="dot"></span>Chatterly</span>
      <span class="social-item"><span class="dot"></span>Pixlora</span>
      <span class="social-item"><span class="dot"></span>Quibber</span>
      <span class="line"></span>
    </div>
  </section>

</main>
</body>
</html>
```